Clear Harbor Business card

We are a company that owns 2 compliance software programs for TV, Radio and Cable industries as well as an online job board. We need a professional business card that incorproates all three logos.

```html
<!DOCTYPE html>
<html lang="en">
<head>
<meta charset="utf-8">
<title>Clear Harbor Business Card</title>
<link rel="stylesheet" href="https://fonts.googleapis.com/css2?family=Roboto:wght@400;700;900&family=Roboto+Condensed:wght@400;700&display=swap">
<style>
  :root {
    --navy: #2f2b86;
    --orange: #e8532b;
    --paper: #ffffff;
    --stage: #e9e6e1;
  }
  * { box-sizing: border-box; margin: 0; padding: 0; }
  html, body { width: 1200px; height: 780px; overflow: hidden; background: var(--stage); }
  body { font-family: "Roboto", Arial, sans-serif; position: relative; }

  .card {
    position: absolute;
    width: 560px; height: 320px;
    background: var(--paper);
    border-radius: 16px;
    overflow: hidden;
    box-shadow: 0 6px 18px rgba(0,0,0,.18);
    top: 230px;
  }
  .card--front { left: 30px; }
  .card--back  { left: 610px; }
  .card svg.bands { position: absolute; inset: 0; }

  .brand-row {
    position: absolute;
    display: flex; align-items: center; gap: 14px;
  }
  .card--front .brand-row { left: 26px; top: 36px; }
  .card--back  .brand-row { left: 0; right: 0; top: 136px; justify-content: center; }

  .brand {
    font-family: "Roboto", Arial, sans-serif;
    font-weight: 900;
    font-size: 17px;
    line-height: 1.05;
    color: var(--navy);
    display: flex; align-items: center; gap: 6px;
  }
  .brand__dot { width: 10px; height: 10px; background: var(--orange); border-radius: 50%; flex: none; }
  .brand-divider { width: 1px; height: 46px; background: var(--navy); }

  .contact { position: absolute; left: 34px; top: 170px; color: var(--navy); font-family: "Roboto Condensed", Arial, sans-serif; }
  .contact__name { font-size: 19px; font-weight: 700; letter-spacing: .3px; }
  .contact__role { color: var(--orange); font-weight: 400; font-size: 17px; }
  .contact__sep { color: var(--navy); font-weight: 400; margin: 0 4px; }
  .contact__line { display: flex; align-items: center; gap: 7px; font-size: 15px; margin-top: 4px; }
  .contact__icon { width: 10px; height: 10px; flex: none; }

  .address {
    position: absolute; right: 34px; top: 90px;
    text-align: right;
    font-family: "Roboto Condensed", Arial, sans-serif;
    font-size: 14px; line-height: 1.35; color: var(--navy);
  }

  .website {
    position: absolute; right: 30px; bottom: 26px;
    color: #ffffff; font-size: 14px; letter-spacing: 2.5px;
  }
</style>
</head>
<body>

  <section class="card card--front" aria-label="Business card front">
    <svg class="bands" width="560" height="320" viewBox="0 0 560 320" aria-hidden="true">
      <line x1="34" y1="162" x2="545" y2="138" stroke="var(--orange)" stroke-width="1"/>
      <path d="M0,262 C230,258 420,206 560,110 L560,126 C420,222 230,274 0,282 Z" fill="var(--orange)"/>
      <path d="M0,292 C240,288 430,236 560,150 L560,320 L0,320 Z" fill="var(--navy)"/>
    </svg>

    <div class="brand-row">
      <span class="brand">Clear Harbor<br>Broadcast</span>
      <span class="brand-divider"></span>
      <span class="brand">Clear Harbor<br>Cable</span>
      <span class="brand-divider"></span>
      <span class="brand"><span class="brand__dot"></span>CrewListing.com</span>
    </div>

    <div class="address">PO BOX 456, Harbor Road<br>3rd Lane, Arizona</div>

    <div class="contact">
      <div class="contact__name">DANA HOLLIS<span class="contact__sep">|</span><span class="contact__role">Director</span></div>
      <div class="contact__line">
        <svg class="contact__icon" viewBox="0 0 10 10" aria-hidden="true"><rect x="1" y="1" width="8" height="8" fill="none" stroke="var(--navy)" stroke-width="1.4"/></svg>
        (555) 010 2040
      </div>
      <div class="contact__line">
        <svg class="contact__icon" viewBox="0 0 10 10" aria-hidden="true"><rect x="0.5" y="1.5" width="9" height="7" fill="var(--orange)"/><path d="M0.5,1.5 L5,5.5 L9.5,1.5" fill="none" stroke="#fff" stroke-width="1"/></svg>
        info@clearharbormail.com
      </div>
    </div>

    <div class="website">www.clearharborweb.com</div>
  </section>

  <section class="card card--back" aria-label="Business card back">
    <svg class="bands" width="560" height="320" viewBox="0 0 560 320" aria-hidden="true">
      <path d="M0,0 L560,0 L560,26 C380,30 180,60 0,110 Z" fill="var(--navy)"/>
      <path d="M0,128 C180,78 380,44 560,40 L560,48 C380,54 180,92 0,140 Z" fill="var(--orange)"/>
      <path d="M0,272 C200,266 400,236 560,190 L560,198 C400,248 200,280 0,288 Z" fill="var(--orange)"/>
      <path d="M0,300 C200,294 400,262 560,212 L560,320 L0,320 Z" fill="var(--navy)"/>
    </svg>

    <div class="brand-row">
      <span class="brand">Clear Harbor<br>Broadcast</span>
      <span class="brand-divider"></span>
      <span class="brand">Clear Harbor<br>Cable</span>
      <span class="brand-divider"></span>
      <span class="brand"><span class="brand__dot"></span>CrewListing.com</span>
    </div>
  </section>

</body>
</html>
```